Business Card & Email Signature Design || Upmarket + Luxury

Rima Vale Honey, a New Zealand Manuka Honey company needs a Business Card & Email Signature design.

Our logo's are attached in Gold & Black versions, feel free to be creative with how you use the logo and it's patterns in your design.

Style:
- Looking for an Elegant, Luxurious, Upmarket feel.
- Black/Matte Black Card, Gold Foil, UV Embossing

Information to Add:

- Logo
- Company Name: Rima Vale Honey
- Name: Martin Holloway
- Title: Creative Director
- Phone: +64 2815 96 417
- Email: martin@rimavalehoney.example.nz
- Website: www.rimavalehoney.example.nz

- Socials: ***For email Signature Only***
- Facebook: https://www.facebook.com/rimavalehoney/
- Instagram: https://www.instagram.com/rimavalehoney/

Target Market(s)

Asia/Europe Luxury, Upmarket

Contact Information for Business Card

- Logo
- Name: Martin Holloway
- Phone: +64 2815 96 417

Font styles to use
Other font styles liked:
• Champagne & Limousines (Attached)

Requirements
Must have
• Business Card & Email Signature Design.

Looking for a Sleek, Luxury, Upmarket Design.

```html
<!DOCTYPE html>
<html lang="en">
<head>
<meta charset="utf-8">
<title>Rima Vale Honey — Business Card</title>
<link href="https://fonts.googleapis.com/css2?family=Josefin+Sans:wght@300&family=Open+Sans:wght@400;600&display=swap" rel="stylesheet">
<style>
  :root {
    --backdrop: #2a2a2a;
    --backdrop-edge: #1c1c1c;
    --card-black: #141414;
    --card-edge: #0b0b0b;
    --emboss-hi: #1d1d1d;
    --emboss-lo: #111111;
    --gold: #d9b35f;
    --gold-soft: #c9a455;
  }
  * { box-sizing: border-box; margin: 0; padding: 0; }
  html, body { width: 1200px; height: 1017px; overflow: hidden; }
  body {
    background: radial-gradient(ellipse at 50% 40%, var(--backdrop) 0%, var(--backdrop-edge) 100%);
    position: relative;
  }
  .card {
    position: absolute;
    width: 560px;
    height: 320px;
    background: var(--card-black);
    border-radius: 3px;
    box-shadow: 0 0 0 1px var(--card-edge), 0 24px 50px rgba(0,0,0,0.55);
    overflow: hidden;
  }
  .card--front { left: 90px; top: 150px; }
  .card--back { left: 550px; top: 545px; }

  .emboss-pattern {
    position: absolute;
    border-radius: 50%;
    background: radial-gradient(ellipse at 45% 45%, var(--emboss-hi) 0%, var(--emboss-lo) 70%, transparent 72%);
  }
  .card--front .emboss-pattern { left: 40px; top: 50px; width: 250px; height: 220px; }
  .card--back .emboss-pattern { left: 300px; top: 20px; width: 230px; height: 205px; }

  .brand {
    position: absolute;
    left: 318px;
    top: 146px;
    display: flex;
    align-items: center;
    gap: 12px;
  }
  .brand__dot {
    width: 16px; height: 16px;
    border-radius: 50%;
    background: var(--gold);
  }
  .brand__name {
    font-family: "Josefin Sans", sans-serif;
    font-weight: 300;
    font-size: 17px;
    letter-spacing: 0.22em;
    color: var(--gold);
    text-transform: uppercase;
  }

  .contact {
    position: absolute;
    left: 36px;
    bottom: 34px;
    font-family: "Open Sans", sans-serif;
    color: var(--gold);
  }
  .contact__name {
    font-weight: 600;
    font-size: 19px;
    letter-spacing: 0.04em;
    text-transform: uppercase;
  }
  .contact__title {
    font-size: 13px;
    color: var(--gold-soft);
    margin: 2px 0 12px;
  }
  .contact__list { list-style: none; }
  .contact__item {
    display: flex;
    align-items: center;
    gap: 9px;
    font-size: 12.5px;
    line-height: 19px;
    color: var(--gold-soft);
  }
  .contact__icon { width: 11px; height: 11px; flex: none; }
</style>
</head>
<body>

<section class="card card--front" aria-label="Card front">
  <div class="emboss-pattern" role="img" aria-label="Blind-embossed decorative bee pattern"></div>
  <div class="brand">
    <span class="brand__dot"></span>
    <span class="brand__name">Rima Vale Honey</span>
  </div>
</section>

<section class="card card--back" aria-label="Card back">
  <div class="emboss-pattern" role="img" aria-label="Blind-embossed decorative bee pattern"></div>
  <div class="contact">
    <p class="contact__name">Martin Holloway</p>
    <p class="contact__title">Creative Director</p>
    <ul class="contact__list">
      <li class="contact__item">
        <svg class="contact__icon" viewBox="0 0 12 12"><path d="M2.5 0.8 L4.6 3.2 L3.6 4.6 Q4.6 6.9 7.4 8.4 L8.8 7.4 L11.2 9.5 L9.8 11.2 Q4.8 11 0.8 2.2 Z" fill="var(--gold)"/></svg>
        <span>+64 2815 96 417</span>
      </li>
      <li class="contact__item">
        <svg class="contact__icon" viewBox="0 0 12 12"><rect x="0.5" y="2" width="11" height="8" fill="var(--gold)"/><path d="M0.8 2.4 L6 6.6 L11.2 2.4" stroke="var(--card-black)" stroke-width="1.1" fill="none"/></svg>
        <span>martin@rimavalehoney.example.nz</span>
      </li>
      <li class="contact__item">
        <svg class="contact__icon" viewBox="0 0 12 12"><circle cx="6" cy="6" r="5.5" fill="var(--gold)"/><path d="M0.5 6 H11.5 M6 0.5 Q2.8 6 6 11.5 M6 0.5 Q9.2 6 6 11.5" stroke="var(--card-black)" stroke-width="0.9" fill="none"/></svg>
        <span>www.rimavalehoney.example.nz</span>
      </li>
    </ul>
  </div>
</section>

</body>
</html>
```